Laser Tattoo Removal Business Cards

We are looking for a professional business card design for a laser tattoo removal business. Ideally looking for a black business card design. The name of the business is Brightline Tattoo Removal. We place our cards at local tattoo shops so we ideally are looking for something trendy/edgy to draw both male and female clientele in.

Target Market(s)

Male/Female ages 18-60

Contact Information for Business Card

black background ideally.. hoping to stay within greys, whites and black

Font styles to use
Serif
Sans Serif

Colors
121212
a9a9a9
5c5c5c
f5f5f5
ffffff
7f7f7f
606060
848484
9d9d9d

Requirements
Must have
• Employee Info:
• Melissa Thornbury
• Chief Executive Offer
• m: 919.537.2846
• w: 919.362.4178
• f: 919.685.3907
• mthornbury@brightlinetattooremoval.example
• Address:
• 4615 Oakmere Pkwy, Suite 210
• Raleigh, NC 27654
• Website:
• www.brightlinetattooremoval.example
Nice to have
• Myabe business name on back or logo on back and employee info on the front

```html
<!DOCTYPE html>
<html lang="en">
<head>
<meta charset="utf-8">
<title>Brightline Tattoo Removal – Business Cards</title>
<link href="https://fonts.googleapis.com/css2?family=Roboto:wght@400&family=Roboto+Condensed:wght@500;700&display=swap" rel="stylesheet">
<style>
  :root {
    --stage: #3a3a3a;
    --card-light: #e2e2e2;
    --card-light-deep: #d4d4d4;
    --card-dark: #1c1c1e;
    --ink: #121212;
    --ink-soft: #5c5c5c;
    --ink-muted: #7f7f7f;
    --white: #ffffff;
  }
  * { margin: 0; padding: 0; box-sizing: border-box; }
  html, body { width: 1200px; height: 960px; overflow: hidden; }
  body { background: var(--stage); position: relative; font-family: "Roboto", Arial, sans-serif; }

  .card {
    position: absolute;
    left: 322px;
    width: 600px;
    height: 342px;
    box-shadow: 0 4px 10px rgba(0,0,0,.45);
  }
  .card--front { top: 108px; overflow: hidden; }
  .card--back { top: 494px; height: 340px; background: var(--card-dark); }

  .card-pattern {
    position: absolute; inset: 0;
    background: radial-gradient(ellipse at 50% 40%, var(--card-light) 0%, var(--card-light-deep) 100%);
  }

  .holder { position: absolute; right: 25px; top: 27px; text-align: right; }
  .holder-name {
    font-family: "Roboto Condensed", Arial, sans-serif;
    font-weight: 700; font-size: 21px; color: var(--ink); letter-spacing: .2px;
  }
  .holder-title { font-size: 14.5px; color: var(--ink-muted); margin-top: 2px; }
  .holder-tab { position: absolute; right: 0; top: 29px; width: 9px; height: 40px; background: var(--ink); }

  .contact { position: absolute; left: 31px; top: 202px; list-style: none; }
  .contact li {
    display: flex; align-items: center; height: 19px;
    font-size: 14px; color: var(--ink-soft);
  }
  .contact svg { width: 14px; height: 14px; margin-right: 9px; fill: var(--ink); }
  .address { position: absolute; left: 30px; top: 300px; font-size: 14px; color: var(--ink-soft); }

  .wordmark {
    position: absolute; left: 0; right: 0; top: 150px;
    text-align: center;
    font-family: "Roboto Condensed", Arial, sans-serif;
    font-weight: 500; font-size: 30px; letter-spacing: 2px;
    color: var(--white); text-transform: uppercase;
  }
</style>
</head>
<body>

<section class="card card--front">
  <div class="card-pattern" role="img" aria-label="Soft grey damask pattern across the card face"></div>

  <div class="holder">
    <div class="holder-name">MELISSA THORNBURY</div>
    <div class="holder-title">Chief Executive Offer</div>
  </div>
  <div class="holder-tab"></div>

  <ul class="contact">
    <li><svg viewBox="0 0 24 24"><path d="M6.6 10.8a15.1 15.1 0 0 0 6.6 6.6l2.2-2.2c.3-.3.7-.4 1-.2 1.1.4 2.3.6 3.6.6.6 0 1 .4 1 1V20c0 .6-.4 1-1 1A17 17 0 0 1 3 4c0-.6.4-1 1-1h3.5c.6 0 1 .4 1 1 0 1.3.2 2.5.6 3.6.1.3 0 .7-.2 1z"/></svg>919.362.4178</li>
    <li><svg viewBox="0 0 24 24"><path d="M7 1h10a2 2 0 0 1 2 2v18a2 2 0 0 1-2 2H7a2 2 0 0 1-2-2V3a2 2 0 0 1 2-2zm0 3v14h10V4z"/></svg>919.537.2846</li>
    <li><svg viewBox="0 0 24 24"><path d="M6 2h12v6H6zM3 9h18a2 2 0 0 1 2 2v7h-4v4H5v-4H1v-7a2 2 0 0 1 2-2zm4 7v4h10v-4z"/></svg>919.685.3907</li>
    <li><svg viewBox="0 0 24 24"><path d="M2 5h20v14H2zm2 2v.5l8 5 8-5V7z"/></svg>mthornbury@brightlinetattooremoval.example</li>
    <li><svg viewBox="0 0 24 24"><path d="M12 2a10 10 0 1 0 0 20 10 10 0 0 0 0-20zm-1 17.9A8 8 0 0 1 4.2 10L9 15v1a2 2 0 0 0 2 2zm6.9-2.5A2 2 0 0 0 16 16h-1v-3a1 1 0 0 0-1-1H8v-2h2a1 1 0 0 0 1-1V7h2a2 2 0 0 0 2-2v-.4a8 8 0 0 1 2.9 12.8z"/></svg>www.brightlinetattooremoval.example</li>
  </ul>
  <div class="address">4615 Oakmere Pkwy, Suite 210, Raleigh, NC 27654</div>
</section>

<section class="card card--back">
  <div class="wordmark">Brightline Tattoo Removal</div>
</section>

</body>
</html>
```